Business card for my new company (Accounting firm)

I need a business card for my new business Brightwell Advisory and Ledger SA. Our services are accounting, tax, audit and financial management. Our customers are small companies, start-ups and new companies. The final design has to show financial security, trust and growth. Please find our logo attached to the business card. Text for the business card: Brightwell Advisory and Ledger SA Tomas Varenholt Director and Founder Certified Accountant Tel. 022 418 57 34 tv@clairevalconseil.ch www.clairevalconseil.ch Rue des Vergières 27 1201 Geneva
Target Market(s)
Our customers are small companies, start-ups and new companies.
Industry/Entity Type
Finance And Accounting
Contact Information for Business Card
Claireval Conseil et Comptes SA
Tomas Varenholt
Directeur et Fondateur
Expert-comptable diplômé
Tél. 022 418 57 34
tv@clairevalconseil.ch
www.clairevalconseil.ch
Rue des Vergières 27
1201 Genève

```html
<!DOCTYPE html>
<html lang="en">
<head>
<meta charset="utf-8">
<title>Claireval Conseil et Comptes SA — Business Card</title>
<link rel="stylesheet" href="https://fonts.googleapis.com/css2?family=Lato:wght@400;700&family=Montserrat:wght@500&display=swap">
<style>
  :root {
    --backdrop: #d9d9d9;
    --blue-deep: #1a7fc4;
    --blue-bright: #2ea9e0;
    --blue-dark: #17649a;
    --charcoal: #3d3d3e;
    --white: #ffffff;
    --shadow: rgba(0, 0, 0, 0.35);
  }
  * { box-sizing: border-box; margin: 0; padding: 0; }
  html, body {
    width: 1200px;
    height: 802px;
    overflow: hidden;
    background: var(--backdrop);
  }
  .card {
    position: absolute;
    top: 274px;
    width: 443px;
    height: 265px;
    box-shadow: 2px 3px 6px var(--shadow);
    overflow: hidden;
  }
  .card-front {
    left: 136px;
    background: var(--white);
    font-family: "Lato", sans-serif;
  }
  .info-panel {
    position: absolute;
    left: 0;
    top: 0;
    width: 292px;
    height: 100%;
    background: linear-gradient(180deg, var(--blue-deep) 0%, var(--blue-bright) 45%, var(--blue-bright) 70%, var(--blue-dark) 100%);
    color: var(--white);
    padding: 37px 0 0 23px;
  }
  .holder-name {
    font-weight: 700;
    font-size: 15.5px;
    letter-spacing: -0.2px;
    line-height: 1;
  }
  .holder-role {
    font-size: 12.5px;
    line-height: 15.5px;
    margin-top: 2px;
  }
  .contact-list {
    list-style: none;
    margin-top: 23px;
    font-size: 12.5px;
    line-height: 16px;
  }
  .contact-list li {
    display: flex;
    align-items: center;
    gap: 9px;
  }
  .contact-icon {
    width: 12px;
    height: 12px;
    flex: none;
  }
  .address {
    font-style: normal;
    font-size: 12.5px;
    line-height: 16px;
    margin-top: 15px;
  }
  .brand-block {
    position: absolute;
    left: 292px;
    top: 0;
    width: 151px;
    height: 100%;
    display: flex;
    flex-direction: column;
    align-items: center;
    justify-content: center;
    gap: 12px;
    text-align: center;
  }
  .brand-block .brand-dot {
    width: 30px;
    height: 30px;
    border-radius: 50%;
    background: var(--blue-bright);
  }
  .brand-block .brand-label {
    font-family: "Lato", sans-serif;
    font-weight: 700;
    font-size: 14px;
    line-height: 18px;
    color: var(--blue-deep);
  }
  .card-back {
    left: 624px;
    background: var(--charcoal);
    display: flex;
    flex-direction: column;
    align-items: center;
    justify-content: center;
    gap: 12px;
  }
  .card-back .brand-dot {
    width: 26px;
    height: 26px;
    border-radius: 50%;
    background: var(--blue-bright);
  }
  .brand-name {
    font-family: "Montserrat", sans-serif;
    font-weight: 500;
    font-size: 15px;
    letter-spacing: 2px;
    text-transform: uppercase;
    color: var(--white);
    text-align: center;
    line-height: 1.4;
  }
</style>
</head>
<body>
  <section class="card card-front">
    <div class="info-panel">
      <h1 class="holder-name">SA TOMAS VARENHOLT</h1>
      <p class="holder-role">Director and Founder<br>Certified Accountant</p>
      <ul class="contact-list">
        <li>
          <svg class="contact-icon" viewBox="0 0 12 12" aria-hidden="true"><path fill="#fff" d="M1 4c0-2 2-3 5-3s5 1 5 3l-2 .5L8 3H4L3 4.5zM3 6h6l1 5H2z"/></svg>
          022 418 57 34
        </li>
        <li>
          <svg class="contact-icon" viewBox="0 0 12 12" aria-hidden="true"><rect x="1" y="2.5" width="10" height="7" fill="#fff"/><path d="M1 2.5l5 4 5-4" fill="none" stroke="#2ea9e0" stroke-width="1"/></svg>
          tv@clairevalconseil.ch
        </li>
        <li>
          <svg class="contact-icon" viewBox="0 0 12 12" aria-hidden="true"><circle cx="6" cy="6" r="5" fill="#fff"/><path d="M3 4c1 0 2 1 2 2s-1 1-1 3M7 2c0 1 1 2 2 2" stroke="#2ea9e0" stroke-width="1" fill="none"/></svg>
          www.clairevalconseil.ch
        </li>
      </ul>
      <address class="address">Rue des Vergières 27<br>1201 Geneva</address>
    </div>
    <div class="brand-block">
      <span class="brand-dot" aria-hidden="true"></span>
      <p class="brand-label">Claireval<br>Conseil et<br>Comptes SA</p>
    </div>
  </section>

  <section class="card card-back">
    <span class="brand-dot" aria-hidden="true"></span>
    <p class="brand-name">Claireval<br>Conseil et Comptes SA</p>
  </section>
</body>
</html>
```